Product labels for new supplements business targeting high performing creative people

I need a label design for different supplements like Whey, BCAA, Melatonin etc. that I could customize for each use case separately.

The brand is called moonquell.life, and it would be the first design of the labels. We haven't sold any products yet, but the target audience is people with growth mindset, people who want to be as efficient as possible and are constantly looking to improve their lifestyle. As part of that, they are also working out, but don't know much about supplements yet. Mostly people between 20-34.

I don't have a too specific idea of the expected design, though it should be light, warm, smart and minimalist, maybe have some patterns. It should looks smart and clean (and expensive). Orange and golden might be the additional colors for white. I have attached the templates of some products that I plan to sell and also the logo of the brand.

Here's what I have used for inspiration:
Brands that I like and are somewhat similar in concept: https://www.vantrel.com/ (!!specially the way they
bring "how the product helps them" in focus, not "what the product is" & https://www.plomi.care/ &
https://www.delvora.com/sport/ & https://en.kalobrine.fr/ &
https://48sketchworks.com/profiles/marenhollowaydesign/designs/617482

Here's how different products look like: https://grenvolt.com/catalog

Target Market(s)

target audience is people with growth mindset, people who want to be as efficient as possible and are constantly looking to improve their lifestyle. As part of that, they are also working out, but don't know much about supplements yet. Mostly people between 20-34.

Industry/Entity Type

Supplements

Font styles to use
Sans Serif

Colors
FFC000
F8CF3A
FAE287
FDF2CF
FEFAEE
F0912C
F2A743
F7CA91
FBE8D2
FDF5EE
EE7325
F08F49
F5BC92
FAE3D3
FDF4ED

Requirements
Must have
• Clean, smart and minimalist design that can be applied for different products in different sizes, like Whey protein, BCAA, vitamins etc. available here: https://grenvolt.com/catalog
Nice to have
• Patterns, expensive look
Should not have
• Doodles, too many colors

```html
<!DOCTYPE html>
<html lang="en">
<head>
<meta charset="utf-8">
<title>moonquell.life supplement labels</title>
<link rel="stylesheet" href="https://fonts.googleapis.com/css2?family=Poppins:wght@400;500;600;700&display=swap">
<style>
  :root {
    --stage: #a4a4a4;
    --paper: #ffffff;
    --cream: #fdf2cf;
    --butter: #fae287;
    --gold: #ebc347;
    --amber: #f2a743;
    --orange: #ee7325;
    --ink: #1f1f1f;
    --grey: #7a7a7a;
    --soft-grey: #8a8a8a;
    --net: #dba84a;
    --line: #f7ca91;
  }
  * { box-sizing: border-box; margin: 0; padding: 0; }
  html, body { width: 1092px; height: 1200px; overflow: hidden; }
  body {
    background: var(--stage);
    font-family: "Poppins", sans-serif;
    color: var(--ink);
  }
  .label-sheet {
    position: absolute;
    left: 30px; top: 338px;
    display: grid;
    grid-template-columns: 500px 500px;
    grid-template-rows: 246px 246px;
    gap: 32px;
  }
  .label {
    position: relative;
    width: 500px; height: 246px;
    overflow: hidden;
    box-shadow: 0 3px 8px rgba(0,0,0,.25);
  }
  .label-ground {
    position: absolute; inset: 0;
    background: linear-gradient(180deg, var(--paper) 0%, var(--paper) 60%, var(--cream) 80%, var(--butter) 100%);
  }
  .label-arc { position: absolute; left: 0; top: 0; width: 500px; height: 246px; }
  .label-row {
    position: absolute; left: 0; right: 0;
    text-align: center; white-space: nowrap;
  }
  .brand {
    top: 22px;
    display: flex; justify-content: center; align-items: center; gap: 6px;
    font-size: 17px; font-weight: 500; color: var(--ink);
  }
  .brand-dot {
    width: 11px; height: 11px; border-radius: 50%;
    background: var(--orange);
  }
  .product-icon { top: 62px; display: flex; justify-content: center; }
  .product-name {
    top: 104px;
    font-size: 38px; font-weight: 700; line-height: 48px;
    color: var(--gold); letter-spacing: 0.5px;
  }
  .product-variant {
    top: 143px;
    font-size: 14px; line-height: 18px; color: var(--grey);
  }
  .product-benefit {
    top: 170px;
    font-size: 8.5px; line-height: 10.5px; color: var(--soft-grey);
  }
  .supplement-tag {
    top: 205px;
    font-size: 12px; font-weight: 600; letter-spacing: 2.6px;
    color: var(--ink);
  }
  .net-content {
    top: 222px;
    font-size: 10px; color: var(--net);
  }
</style>
</head>
<body>
<main class="label-sheet">

  <section class="label">
    <div class="label-ground" role="img" aria-label="Warm white-to-gold background with fine flowing line pattern"></div>
    <svg class="label-arc" viewBox="0 0 500 246" aria-hidden="true"><path d="M0 228 Q250 178 500 214" fill="none" stroke="var(--line)" stroke-width="0.8"/></svg>
    <div class="label-row brand"><span class="brand-dot"></span>moonquell.life</div>
    <div class="label-row product-icon">
      <svg width="43" height="43" viewBox="0 0 43 43" aria-hidden="true">
        <circle cx="21.5" cy="21.5" r="20" fill="none" stroke="var(--amber)" stroke-width="1.4"/>
        <path d="M22 11 A11 11 0 1 0 31 27 A9 9 0 0 1 22 11 Z" fill="none" stroke="var(--amber)" stroke-width="1.3"/>
        <circle cx="26" cy="16" r="1.3" fill="var(--amber)"/>
        <circle cx="24" cy="22" r="1.1" fill="var(--amber)"/>
        <circle cx="28.5" cy="21" r="0.9" fill="var(--amber)"/>
      </svg>
    </div>
    <div class="label-row product-name">MELATONIN</div>
    <div class="label-row product-variant">1 mg</div>
    <div class="label-row product-benefit">Fall asleep faster<br>Stay asleep longer</div>
    <div class="label-row supplement-tag">DIETARY SUPPLEMENT</div>
    <div class="label-row net-content">60 tablets</div>
  </section>

  <section class="label">
    <div class="label-ground" role="img" aria-label="Warm white-to-gold background with fine flowing line pattern"></div>
    <svg class="label-arc" viewBox="0 0 500 246" aria-hidden="true"><path d="M0 228 Q250 178 500 214" fill="none" stroke="var(--line)" stroke-width="0.8"/></svg>
    <div class="label-row brand"><span class="brand-dot"></span>moonquell.life</div>
    <div class="label-row product-icon">
      <svg width="30" height="36" viewBox="0 0 30 36" aria-hidden="true"><path d="M16 1 L3 20 H13 L9 35 L27 13 H17 L22 1 Z" fill="none" stroke="var(--amber)" stroke-width="1.4" stroke-linejoin="round"/></svg>
    </div>
    <div class="label-row product-name">BEFF PROTEIN</div>
    <div class="label-row product-variant">chocolate</div>
    <div class="label-row product-benefit">Hydrolized beef protein with minimum fat content<br>Promotes muscle gain and help maintain muscle mass</div>
    <div class="label-row supplement-tag">DIETARY SUPPLEMENT</div>
    <div class="label-row net-content">Net Wt. 900 g (31.75 oz)</div>
  </section>

  <section class="label">
    <div class="label-ground" role="img" aria-label="Warm white-to-gold background with fine flowing line pattern"></div>
    <svg class="label-arc" viewBox="0 0 500 246" aria-hidden="true"><path d="M0 228 Q250 178 500 214" fill="none" stroke="var(--line)" stroke-width="0.8"/></svg>
    <div class="label-row brand"><span class="brand-dot"></span>moonquell.life</div>
    <div class="label-row product-icon">
      <svg width="30" height="36" viewBox="0 0 30 36" aria-hidden="true"><path d="M16 1 L3 20 H13 L9 35 L27 13 H17 L22 1 Z" fill="none" stroke="var(--amber)" stroke-width="1.4" stroke-linejoin="round"/></svg>
    </div>
    <div class="label-row product-name">MACA ROOT</div>
    <div class="label-row product-variant">powder</div>
    <div class="label-row product-benefit">Help reduce stress<br>Increaces energy and stamina</div>
    <div class="label-row supplement-tag">DIETARY SUPPLEMENT</div>
    <div class="label-row net-content">20 mg</div>
  </section>

  <section class="label">
    <div class="label-ground" role="img" aria-label="Warm white-to-gold background with fine flowing line pattern"></div>
    <svg class="label-arc" viewBox="0 0 500 246" aria-hidden="true"><path d="M0 228 Q250 178 500 214" fill="none" stroke="var(--line)" stroke-width="0.8"/></svg>
    <div class="label-row brand"><span class="brand-dot"></span>moonquell.life</div>
    <div class="label-row product-icon">
      <svg width="30" height="36" viewBox="0 0 30 36" aria-hidden="true"><path d="M16 1 L3 20 H13 L9 35 L27 13 H17 L22 1 Z" fill="none" stroke="var(--amber)" stroke-width="1.4" stroke-linejoin="round"/></svg>
    </div>
    <div class="label-row product-name">BCAA 2:1:1</div>
    <div class="label-row product-variant">wild berry</div>
    <div class="label-row product-benefit">Essencial branshed chain amino acids BCAA<br>Increaces mucle growth, reduces fatique</div>
    <div class="label-row supplement-tag">DIETARY SUPPLEMENT</div>
    <div class="label-row net-content">Net Wt. 300 g (10.58 oz)</div>
  </section>

</main>
</body>
</html>
```